Steadfast Field Crews

We are a underground coal mining labour hire company, needing a website that links into our online payroll (www.wagelinkr.com.au) and also need to have job applications page that is a preform with drop down menu,s with answers or check boxes. We would also need a 3 tier administration access for access to different files.
We are looking for an ongoing relationship with future app integration

Reason: There are a few more designs to come and I'm out at the mine for another week

Industry/Entity Type

Coal Mining

```html
<!DOCTYPE html>
<html lang="en">
<head>
<meta charset="utf-8">
<title>Stedcoal – Steadfast Field Crews</title>
<link href="https://fonts.googleapis.com/css2?family=Arimo:wght@400;700&display=swap" rel="stylesheet">
<style>
:root{
  --navy:#2b3a9a;
  --navy-dark:#232e80;
  --orange:#f47b20;
  --black:#050505;
  --text:#555555;
  --text-dark:#333333;
  --footer:#1e2026;
  --white:#ffffff;
  --red:#c8281e;
  --green:#3aa548;
}
*{box-sizing:border-box;margin:0;padding:0}
html,body{width:909px;height:1200px;overflow:hidden;background:var(--white)}
body{position:relative;font-family:"Arimo",Arial,sans-serif;color:var(--text)}
.abs{position:absolute}

.topline{left:0;top:0;width:909px;height:6px;background:var(--navy)}
.header{left:0;top:6px;width:909px;height:76px;background:var(--black)}
.brand{left:152px;top:22px;display:flex;align-items:center;gap:8px}
.brand-mark{width:30px;height:30px;border-radius:50%;background:var(--orange)}
.brand-name{font-size:13px;font-weight:700;color:var(--orange);line-height:1.1;width:90px}
.phone{left:620px;top:36px;display:flex;align-items:center;gap:8px;color:var(--white);font-size:11.5px;font-weight:700}
.search{left:729px;top:33px;width:28px;height:21px;background:var(--white);display:flex;align-items:center;justify-content:center}

.nav{left:0;top:82px;width:909px;height:32px;background:var(--navy)}
.nav a{position:absolute;top:0;height:32px;line-height:32px;font-size:6.8px;color:var(--white);text-decoration:none;text-transform:uppercase}
.nav a.active{background:var(--orange);width:78px;text-align:center}
.navline{left:0;top:114px;width:909px;height:2px;background:var(--orange)}

.slider{left:0;top:116px;width:909px;height:330px;background:radial-gradient(ellipse at 55% 45%,#6b6a63 0%,#3d3c38 45%,#1c1c1a 100%)}
.slide-panel{left:152px;top:200px;width:262px;height:152px;background:rgba(48,58,140,.72);padding:24px 0 0 10px}
.slide-panel li{list-style:none;display:flex;align-items:center;gap:10px;color:var(--white);font-size:11px;height:22px}
.slide-panel li::before{content:"";width:7px;height:7px;border-radius:50%;background:var(--red);flex:none}
.dots{left:441px;top:428px;display:flex;gap:5px}
.dots span{width:8px;height:8px;border-radius:50%;background:var(--white)}
.dots span.on{background:var(--navy);box-shadow:0 0 0 1px var(--white)}

.welcome-title{left:0;top:468px;width:909px;text-align:center;font-size:15px;color:var(--navy)}
.welcome-title span{color:var(--orange)}
.welcome-text{left:152px;top:498px;width:382px;font-size:7.2px;line-height:14.4px;color:var(--text)}
.welcome-photo{left:559px;top:489px;width:198px;height:82px;background:linear-gradient(135deg,#8e8f92,#4e5054 60%,#2a2b2d)}

.tile{width:282px;height:134px}
.tile .band{position:absolute;left:0;top:47px;width:100%;height:36px;background:rgba(244,123,32,.85);color:var(--white);font-size:12px;display:flex;align-items:center;justify-content:center}
.tile-eng{left:151px;top:597px;background:linear-gradient(135deg,#6a4a2a,#2a2420 60%,#4a3a2e)}
.tile-svc{left:473px;top:597px;background:linear-gradient(135deg,#3c3a36,#1e1c1a 55%,#5a3a20)}
.tile-coal{left:151px;top:756px;background:linear-gradient(135deg,#c45a20,#8a3a1c 50%,#3a3a32)}
.tile-under{left:473px;top:756px;background:radial-gradient(ellipse at 70% 70%,#9a9a9a,#3a3a3a 45%,#121212)}

.h2{font-size:14px;color:var(--orange);font-weight:400}
.services-title{left:150px;top:912px}
.services-text{left:152px;top:939px;width:410px;font-size:6.8px;line-height:10.8px;color:var(--text)}
.ticks li{position:absolute;list-style:none;font-size:8px;line-height:14px;color:var(--text-dark);padding-left:18px;width:190px}
.ticks li svg{position:absolute;left:0;top:3px}

.news-title{left:584px;top:910px}
.news-box{left:586px;top:940px;width:169px;height:83px;background:#f4f4f4;border:1px solid #dcdcdc;border-left:2px solid var(--navy);padding:8px 10px 0 12px;font-size:6.8px;line-height:10.8px;color:var(--text)}
.news-box h3{font-size:7px;color:var(--red);font-weight:700;margin-bottom:3px}
.news-box a{color:var(--navy);text-decoration:none}
.jobs{left:586px;top:1031px;width:169px;height:66px;background:var(--orange);border:1px solid #e06a10}
.jobs h3{position:absolute;left:14px;top:12px;font-size:10.5px;font-weight:400;color:var(--navy)}
.jobs .partner{position:absolute;left:10px;top:38px;display:flex;align-items:center;gap:5px;font-size:12px;color:var(--white)}
.jobs .partner i{width:10px;height:10px;background:var(--navy);display:block}
.jobs .apply{position:absolute;left:101px;top:37px;width:63px;height:19px;background:var(--navy);color:var(--white);font-size:8px;font-weight:700;display:flex;align-items:center;justify-content:center}

.footline{left:0;top:1115px;width:909px;height:5px;background:var(--orange)}
.footer{left:0;top:1120px;width:909px;height:80px;background:var(--footer)}
.foot-links{left:153px;top:1142px;font-size:7px;color:var(--white)}
.foot-copy{left:152px;top:1163px;font-size:7px;color:var(--white)}
.social{top:1142px;width:23px;height:23px;border-radius:50%;background:#d8d8d8}
</style>
</head>
<body>
<div class="abs topline"></div>
<header class="abs header"></header>
<div class="abs brand"><span class="brand-mark"></span><span class="brand-name">Steadfast Field Crews</span></div>
<div class="abs phone">
  <svg width="14" height="14" viewBox="0 0 14 14"><path d="M3 1c1 0 2 2.5 2 3s-1.5 1-1.3 2c.4 1.6 2 3.2 3.6 3.6 1 .2 1.5-1.3 2-1.3s3 1 3 2-1.5 2.5-3 2.5C5 12.8 1.2 9 1 4 1 2.5 2 1 3 1z" fill="#f47b20"/></svg>
  90198765432
</div>
<div class="abs search"><svg width="11" height="11" viewBox="0 0 11 11"><circle cx="4.5" cy="4.5" r="3.3" fill="none" stroke="#111" stroke-width="1.4"/><line x1="7" y1="7" x2="10" y2="10" stroke="#111" stroke-width="1.6"/></svg></div>

<nav class="abs nav">
  <a class="active" href="#" style="left:152px">Home</a>
  <a href="#" style="left:241px">Apply for position</a>
  <a href="#" style="left:349px">Pay portal</a>
  <a href="#" style="left:428px">Download</a>
  <a href="#" style="left:509px">Mission</a>
  <a href="#" style="left:578px">About us</a>
  <a href="#" style="left:652px">Contact us</a>
</nav>
<div class="abs navline"></div>

<section class="abs slider" role="img" aria-label="Miner walking beside a loader in an underground coal tunnel"></section>
<ul class="abs slide-panel">
  <li>Roadheader Drivage / Tunnel Excavation</li>
  <li>Labour Hire</li>
  <li>Mining Equipment Hire</li>
  <li>Training and Training Development</li>
  <li>Mining Contracts / Project Management</li>
</ul>
<svg class="abs" style="left:48px;top:253px" width="14" height="22" viewBox="0 0 14 22"><path d="M12 2 4 11l8 9" fill="none" stroke="#f47b20" stroke-width="4"/></svg>
<svg class="abs" style="left:839px;top:253px" width="14" height="22" viewBox="0 0 14 22"><path d="M2 2l8 9-8 9" fill="none" stroke="#f47b20" stroke-width="4"/></svg>
<div class="abs dots"><span class="on"></span><span></span><span></span></div>

<h1 class="abs welcome-title" style="font-weight:400">Welcome To <span>Stedcoal</span></h1>
<p class="abs welcome-text">We are SFCL pty ltd trading as Steadfast Field Crews, we are experienced in ground consolidation in underground coal mines, in short when they collapse or cave in we come in with chemical pumps and stabilise the ground or fill cavities which will then allow for the mining process to continue. We also do general mine labor as well. We are a labor hire company for major mining services company, we offer labor solutions in New South Wales and Queensland in the underground coal mines.</p>
<div class="abs welcome-photo" role="img" aria-label="Excavator loading a dump truck at an open coal pit"></div>

<div class="abs tile tile-eng" role="img" aria-label="Miner with headlamp working on machinery"><div class="band">Engineering</div></div>
<div class="abs tile tile-svc" role="img" aria-label="Crew in orange hi-vis underground"><div class="band">Services</div></div>
<div class="abs tile tile-coal" role="img" aria-label="Rescue team in orange overalls and hard hats"><div class="band">Coal Minning</div></div>
<div class="abs tile tile-under" role="img" aria-label="Lit mine tunnel with roof supports"><div class="band">Underground</div></div>

<h2 class="abs h2 services-title">Services</h2>
<p class="abs services-text">Lorem ipsum dolor sit amet, consectetur adipiscing elit. Nulla convallis egestas rhoncus. Donec facilisis fermentum sem, ac viverra ante luctus vel. Donec vel mauris quam. Lorem ipsum dolor sit amet, consectetur adipiscing elit. Nulla convallis egestas rhoncus. Donec facilisis fermentum sem, ac viverra ante luctus vel. Donec vel mauris quam. Lorem ipsum dolor sit amet, consectetur adipiscing elit. Nulla convallis egestas rhoncus. Donec facilisis fermentum sem, ac viverra ante luctus vel. Donec vel mauris quam. Lorem ipsum dolor sit amet, consectetur adipiscing elit. Nulla convallis egestas rhoncus. Donec facilisis fermentum sem, ac viverra ante luctus vel. Donec vel mauris quam.</p>
<ul class="ticks">
  <li style="left:152px;top:1016px"><svg width="10" height="8" viewBox="0 0 10 8"><path d="M1 4l3 3 5-6" fill="none" stroke="#3aa548" stroke-width="1.8"/></svg>Market Research</li>
  <li style="left:152px;top:1035px;width:130px"><svg width="10" height="8" viewBox="0 0 10 8"><path d="M1 4l3 3 5-6" fill="none" stroke="#3aa548" stroke-width="1.8"/></svg>Channel Distribution &amp; Development</li>
  <li style="left:152px;top:1068px"><svg width="10" height="8" viewBox="0 0 10 8"><path d="M1 4l3 3 5-6" fill="none" stroke="#3aa548" stroke-width="1.8"/></svg>Sales/Market Representation</li>
  <li style="left:152px;top:1085px"><svg width="10" height="8" viewBox="0 0 10 8"><path d="M1 4l3 3 5-6" fill="none" stroke="#3aa548" stroke-width="1.8"/></svg>Project-Based Market Research</li>
  <li style="left:340px;top:1016px"><svg width="10" height="8" viewBox="0 0 10 8"><path d="M1 4l3 3 5-6" fill="none" stroke="#3aa548" stroke-width="1.8"/></svg>Information Forum Events</li>
  <li style="left:340px;top:1035px"><svg width="10" height="8" viewBox="0 0 10 8"><path d="M1 4l3 3 5-6" fill="none" stroke="#3aa548" stroke-width="1.8"/></svg>Business Plans</li>
  <li style="left:340px;top:1054px"><svg width="10" height="8" viewBox="0 0 10 8"><path d="M1 4l3 3 5-6" fill="none" stroke="#3aa548" stroke-width="1.8"/></svg>Marketing Plans</li>
  <li style="left:340px;top:1071px"><svg width="10" height="8" viewBox="0 0 10 8"><path d="M1 4l3 3 5-6" fill="none" stroke="#3aa548" stroke-width="1.8"/></svg>Workshops and Seminars</li>
</ul>

<h2 class="abs h2 news-title">Latest News</h2>
<article class="abs news-box">
  <h3>Deepseam Re Brands</h3>
  Lorem ipsum dolor sit amet, consectetur adipiscing elit. Nulla convallis egestas rhoncus. Donec facilisis fermentum sem, ac viverra ante luctus vel. Donec vel mauris<br>
  <a href="#">Read more..</a>
</article>
<div class="abs jobs">
  <h3>Job Vacancies</h3>
  <div class="partner"><i></i>wagelinkr</div>
  <div class="apply">Apply Now</div>
</div>

<div class="abs footline"></div>
<footer class="abs footer"></footer>
<div class="abs foot-links">Home &nbsp;|&nbsp; About us &nbsp;|&nbsp; Counselling &nbsp;|&nbsp; Workshop &nbsp;|&nbsp; Contact us</div>
<div class="abs foot-copy">Content copyright 2013. Stedcoal. All rights reserved.</div>
<div class="abs social" style="left:681px" aria-label="Social link"></div>
<div class="abs social" style="left:708px" aria-label="Social link"></div>
<div class="abs social" style="left:735px" aria-label="Social link"></div>
</body>
</html>
```